New Website Design & Build Project - Lively Oak Dishes

I am looking for a professional clean looking website design then build of a website for my meal delivery business Lively Oak Dishes. I already have the domain - www.livelyoakdishes.com.au and I will upload brief for the design and layout of the website.

I have a dropbox full of photos, designs, videos and existing graphic design work that I can share with the designers. This can be provided upon designer request.

I am looking to build this site in WORDPRESS and I would like to build the site using the Velmora Page Composer - https://velmoraskins.example/

Target Market(s)

Kids from 2-16 , Teenagers - 16 - 19, Adults - 19 - 80 + - We Cater For Everyone

Industry/Entity Type

Health And Wellness

Coding

Coded - Design and coding required

Number of Pages Required

5+ page

Colors
33b8a4
abd037
ec1f27
fbee3f
3276b5

Requirements
Must have
• Must incorporate the included Lively Oak Dishes & LOD Logo
Must incorporate designs of packaging into website design.
Must keep text styles consistant throughout design
Must be mobile, tablet and desktop view responsive on all devices.
Must be built in Wordpress
The coder must have experience with velmora skins, velmora page composer, velmora prospects and also be very experienced with setting up products using Quillo Storefront plug in-
https://quillostorefront.example/
I want to integrate Postwren - https://dealbarn.example/postwren/ into site as well
Nice to have
• All of the above
Should not have
• No dark colours

```html
<!DOCTYPE html>
<html lang="en">
<head>
<meta charset="utf-8">
<title>Lively Oak Dishes</title>
<link rel="stylesheet" href="https://fonts.googleapis.com/css2?family=Open+Sans:wght@400;600;700&family=Lato:wght@400;700&family=Montserrat:wght@400;500;600&family=Raleway:wght@400&display=swap">
<style>
:root{
  --hero-bg:#e6f4f1;
  --plan-bg:#33b8a4;
  --plan-bg-2:#3fa6c4;
  --blue:#3276b5;
  --green:#6dbd45;
  --ink:#1c2b3a;
  --text:#3d3d3d;
  --teal:#1d8ca3;
  --light:#f1f1f1;
  --footer:#3276b5;
  --footer-2:#3a86c2;
  --white:#ffffff;
}
*{margin:0;padding:0;box-sizing:border-box}
html,body{width:1200px;height:3579px;overflow:hidden}
body{position:relative;background:var(--white);font-family:"Lato",sans-serif;color:var(--text)}
.abs{position:absolute}
.btn{position:absolute;display:flex;align-items:center;justify-content:center;border-radius:24px;background:var(--green);color:var(--white);font-family:"Open Sans",sans-serif;font-weight:600;font-size:17px;text-transform:uppercase;white-space:nowrap}

/* header */
.site-header{position:absolute;left:0;top:0;width:1200px;height:92px;background:var(--white)}
.brand{position:absolute;left:108px;top:30px;display:flex;align-items:center;gap:10px;font-family:"Open Sans",sans-serif;font-weight:700;font-size:24px;color:var(--ink)}
.brand-dot{width:22px;height:22px;border-radius:50%;background:var(--green)}
.nav-link{position:absolute;top:39px;font-family:"Open Sans",sans-serif;font-weight:600;font-size:14px;color:var(--ink)}
.header-divider{position:absolute;left:666px;top:30px;width:1px;height:36px;background:#cfcfcf}
.cart-badge{position:absolute;left:702px;top:24px;width:26px;height:26px;border-radius:50%;background:var(--blue);color:#fff;font-size:13px;display:flex;align-items:center;justify-content:center}
.btn-login{left:775px;top:25px;width:111px;height:39px;background:var(--blue);font-weight:400;font-size:17px}
.btn-signup{left:904px;top:25px;width:179px;height:39px;font-weight:400;font-size:17px}

/* hero */
.hero{position:absolute;left:0;top:92px;width:1200px;height:570px;background:var(--hero-bg)}
.hero-title{position:absolute;left:44px;top:228px;font-family:"Open Sans",sans-serif;font-weight:700;font-size:82px;letter-spacing:-3px;line-height:1;white-space:nowrap;color:var(--blue)}
.plate{position:absolute;left:571px;top:47px;width:478px;height:478px;border-radius:50%;background:#fafafa;box-shadow:0 10px 30px rgba(50,118,181,.25)}
.plate-food{position:absolute;left:83px;top:83px;width:312px;height:312px;border-radius:50%;background:radial-gradient(circle,#e7b75a 0%,#c0603a 55%,#efe2b8 100%)}
.slider-dot{position:absolute;left:1084px;width:12px;height:12px;border-radius:50%;background:var(--blue)}
.slider-dot.active{background:transparent;border:2px solid var(--blue)}

/* subscription */
.subscribe-title{position:absolute;left:111px;top:750px;font-family:"Open Sans",sans-serif;font-weight:700;font-size:35px;color:var(--ink)}
.subscribe-text{position:absolute;left:111px;top:805px;width:660px;font-family:"Raleway","Lato",sans-serif;font-size:18px;line-height:34px;color:#444}
.btn-subscribe{left:868px;top:768px;width:151px;height:47px;font-size:19px}

/* food plan */
.food-plan{position:absolute;left:0;top:940px;width:1200px;height:709px;background:linear-gradient(135deg,var(--plan-bg) 0%,var(--plan-bg-2) 100%)}
.plan-title{position:absolute;left:0;top:1008px;width:1200px;text-align:center;font-family:"Open Sans",sans-serif;font-weight:700;font-size:40px;color:#fff}
.plan-sub{position:absolute;left:0;top:1076px;width:1200px;text-align:center;font-size:20px;line-height:34px;color:#fff}
.plan-card{position:absolute;top:1199px;width:234px;height:352px;background:#fff}
.plan-name{position:absolute;left:0;top:24px;width:100%;text-align:center;font-family:"Open Sans",sans-serif;font-weight:700;font-size:19px;line-height:25px;color:var(--ink)}
.plan-photo{position:absolute;left:39px;top:105px;width:156px;height:156px;border-radius:50%;border:2px solid #ddd}
.plan-price{position:absolute;left:140px;top:177px;width:68px;height:68px;border-radius:50%;background:var(--blue);border:4px solid #fff;box-shadow:0 2px 6px rgba(0,0,0,.25);display:flex;align-items:center;justify-content:center;font-family:"Open Sans",sans-serif;font-weight:700;font-style:italic;font-size:22px;color:#fff}
.plan-join{top:1520px;width:151px;height:47px;font-size:17px}

/* smoothie */
.feature-photo{position:absolute;left:108px;top:1756px;width:392px;height:334px;border:2px solid var(--green);background:linear-gradient(120deg,#d9d4d0 0%,#b8a6b0 45%,#a5648c 100%)}
.feature-title{position:absolute;left:536px;top:1744px;width:560px;font-family:"Open Sans",sans-serif;font-weight:700;font-size:30px;line-height:48px;color:var(--ink)}
.feature-text{position:absolute;left:536px;top:1860px;width:553px;font-family:"Raleway","Lato",sans-serif;font-size:16.5px;line-height:34.3px;color:#444;text-align:justify}
.btn-read{left:531px;top:2153px;width:151px;height:47px;font-size:17px}

/* blog */
.blog{position:absolute;left:0;top:2313px;width:1200px;height:793px;background:var(--light)}
.blog-title{position:absolute;left:0;top:2380px;width:1200px;text-align:center;font-family:"Open Sans",sans-serif;font-weight:600;font-size:30px;color:var(--ink)}
.post{position:absolute;background:#fff;border:1px solid #ddd}
.post-photo{position:absolute}
.post-date{position:absolute;font-family:"Montserrat",sans-serif;font-size:13px;color:var(--teal)}
.post-title{position:absolute;font-family:"Montserrat",sans-serif;font-weight:600;font-size:20px;line-height:27px;color:#222}
.post-text{position:absolute;font-family:"Montserrat",sans-serif;font-size:12.5px;line-height:27px;color:#999}
.post-more{position:absolute;font-family:"Montserrat",sans-serif;font-weight:500;font-size:17px;color:var(--teal)}

/* footer */
.site-footer{position:absolute;left:0;top:3113px;width:1200px;height:466px;background:linear-gradient(180deg,var(--footer-2),var(--footer))}
.footer-brand{position:absolute;left:118px;top:3196px;display:flex;align-items:center;gap:10px;font-family:"Open Sans",sans-serif;font-weight:700;font-size:26px;color:#fff}
.footer-about{position:absolute;left:124px;top:3258px;width:260px;font-family:"Raleway","Lato",sans-serif;font-size:18px;line-height:31px;color:#fff}
.social{position:absolute;top:3384px;width:34px;height:34px;border-radius:50%;border:1.5px solid #fff}
.contact-icon{position:absolute;left:458px;width:50px;height:50px;border-radius:50%;background:#fff;display:flex;align-items:center;justify-content:center}
.contact-text{position:absolute;left:537px;font-family:"Raleway","Lato",sans-serif;font-size:19px;line-height:31px;color:#fff}
.footer-link{position:absolute;left:878px;font-family:"Raleway","Lato",sans-serif;font-size:19px;color:#fff}
.footer-link::before{content:"\00BB";font-weight:700;margin-right:12px}
.footer-mark{position:absolute;left:961px;top:3336px;font-family:"Open Sans",sans-serif;font-weight:700;font-size:34px;color:#fff}
.copyright{position:absolute;left:0;top:3516px;width:1200px;text-align:center;font-family:Arial,sans-serif;font-size:14px;color:#fff}
</style>
</head>
<body>

<header class="site-header">
  <div class="brand"><span class="brand-dot"></span>Lively Oak Dishes</div>
  <span class="nav-link" style="left:428px">MENU</span>
  <span class="nav-link" style="left:496px">CONTACT US</span>
  <svg class="abs" style="left:624px;top:34px" width="28" height="28" viewBox="0 0 28 28" fill="none" stroke="#222" stroke-width="3"><circle cx="11" cy="11" r="8"/><line x1="17" y1="17" x2="25" y2="25"/></svg>
  <span class="header-divider"></span>
  <svg class="abs" style="left:680px;top:32px" width="30" height="32" viewBox="0 0 30 32" fill="none" stroke="#222" stroke-width="2"><rect x="3" y="10" width="24" height="20"/><path d="M9 10V7a6 6 0 0 1 12 0v3"/></svg>
  <span class="cart-badge">0</span>
  <span class="btn btn-login">LOGIN</span>
  <span class="btn btn-signup">MEMBER SIGN UP</span>
</header>

<section class="hero">
  <h1 class="hero-title">KIDS MEALS</h1>
  <div class="plate"><div class="plate-food" role="img" aria-label="Plate of spaghetti with meat sauce and parmesan"></div></div>
  <span class="slider-dot" style="top:252px"></span>
  <span class="slider-dot active" style="top:275px"></span>
  <span class="slider-dot" style="top:296px"></span>
  <span class="slider-dot" style="top:319px"></span>
</section>

<h2 class="subscribe-title">LIVELY OAK DISHES SUBSCRIPTION</h2>
<p class="subscribe-text">Join the Lively Oak Dishes subscription service to get the lowest prices. Cancel anytime.</p>
<span class="btn btn-subscribe">JOIN NOW</span>

<section class="food-plan" role="img" aria-label="Backdrop of assorted dishes and bowls on a table"></section>
<h2 class="plan-title">OUR FOOD PLAN</h2>
<p class="plan-sub">Neque porro quisquam est qui dolorem ipsum quia dolor sit amet,<br>consectetur, adipisci velit</p>

<article class="plan-card" style="left:111px">
  <h3 class="plan-name">LOD KIDS 7 DAY<br>MEAL PLAN</h3>
  <div class="plan-photo" role="img" aria-label="Bowl of pasta with cheese" style="background:radial-gradient(circle,#f2c94c,#d8962a)"></div>
  <span class="plan-price">$35</span>
</article>
<article class="plan-card" style="left:357px">
  <h3 class="plan-name">LOD ADULT 7 DAY<br>MEAL PLAN</h3>
  <div class="plan-photo" role="img" aria-label="Grilled chicken with broccoli" style="background:radial-gradient(circle,#6fae3a,#c06a3a)"></div>
  <span class="plan-price">$54</span>
</article>
<article class="plan-card" style="left:606px">
  <h3 class="plan-name">LOD ADULT 7 DAY<br>COUPLES MEAL</h3>
  <div class="plan-photo" role="img" aria-label="Sliced chicken with broccoli and tomato" style="background:radial-gradient(circle,#f5e6d8,#6aab3a)"></div>
  <span class="plan-price" style="font-size:20px">$108</span>
</article>
<article class="plan-card" style="left:853px">
  <h3 class="plan-name">LOD ADULT 21<br>MEALS PER WEEK</h3>
  <div class="plan-photo" role="img" aria-label="Avocado, greens and spices" style="background:radial-gradient(circle,#d6c06a,#5f8a3a)"></div>
  <span class="plan-price" style="font-size:20px">$162</span>
</article>
<span class="btn plan-join" style="left:153px">JOIN NOW</span>
<span class="btn plan-join" style="left:398px">JOIN NOW</span>
<span class="btn plan-join" style="left:647px">JOIN NOW</span>
<span class="btn plan-join" style="left:894px">JOIN NOW</span>

<div class="feature-photo" role="img" aria-label="Mother and daughter eating a packed meal together"></div>
<h2 class="feature-title">THE BEST GREEN SMOOTHIE TO START YOUR DAY</h2>
<p class="feature-text">The King of Green Smoothies would have to be my Superfood Green Smoothie which contains all the elements necessary for unbelievable muscle growth!!! In order to strip off the fat, add lean muscle mass &amp; to provide your body with all the best vitamins &amp; minerals try the following recipe.Once you have mixed it up sit back and read on to discover why this green smoothie is going to help you achieve your goals...... Handful of Ice 1 Banana 1 Handful of Organic Kale 1/3 Lemon 3 Dates 1/4 Cup of Water (Or Cocunut Water to make it sweet.</p>
<span class="btn btn-read">READ MORE</span>

<section class="blog"></section>
<h2 class="blog-title">OAK LIFE BLOG</h2>

<article class="post" style="left:111px;top:2471px;width:319px;height:545px">
  <div class="post-photo" role="img" aria-label="Meal prep containers with vegetables and meat" style="left:0;top:0;width:317px;height:231px;background:linear-gradient(135deg,#a07a58,#d6654a 45%,#8cb04a)"></div>
  <span class="post-date" style="left:32px;top:254px">April,2020</span>
  <h3 class="post-title" style="left:32px;top:283px;width:270px">Sed ut perspiciatis unde omnis iste natus</h3>
  <p class="post-text" style="left:32px;top:352px;width:270px">Ut enim ad minima veniaquis nostreierci tationem ullam corpoboriosan isi utliquid ex ea commodi eprehenderitq ui in ea voluptmmodate velit .</p>
  <span class="post-more" style="left:34px;top:490px">READ MORE &raquo;</span>
</article>

<article class="post" style="left:446px;top:2471px;width:644px;height:265px">
  <div class="post-photo" role="img" aria-label="Fresh vegetables, avocado and grains on a stone surface" style="left:2px;top:2px;width:255px;height:259px;background:linear-gradient(135deg,#8aa84a,#8a969c 60%,#a8b0b6)"></div>
  <span class="post-date" style="left:291px;top:34px">April,2020</span>
  <h3 class="post-title" style="left:291px;top:62px;width:340px">Sed ut perspiciatis unde omnis iste natus error</h3>
  <p class="post-text" style="left:291px;top:121px;width:330px">Ut enim ad minima veniam, quis nostreierci tationem ullam corporis suscipit laboriosan isi ut aliquid ex ea eprehenderitq utate velit .</p>
  <span class="post-more" style="left:295px;top:225px">READ MORE &raquo;</span>
</article>

<article class="post" style="left:446px;top:2750px;width:644px;height:266px">
  <div class="post-photo" role="img" aria-label="Courier handing a paper grocery bag to a customer" style="left:2px;top:2px;width:255px;height:260px;background:linear-gradient(135deg,#eae6e2,#c9a27a 55%,#d8d2cc)"></div>
  <span class="post-date" style="left:291px;top:35px">April,2020</span>
  <h3 class="post-title" style="left:291px;top:63px;width:340px">Sed ut perspiciatis unde omnis iste natus error</h3>
  <p class="post-text" style="left:291px;top:122px;width:330px">Ut enim ad minima veniam, quis nostreierci tationem ullam corporis suscipit laboriosan isi ut aliquid ex ea eprehenderitq utate velit .</p>
  <span class="post-more" style="left:295px;top:226px">READ MORE &raquo;</span>
</article>

<footer class="site-footer"></footer>
<div class="footer-brand"><span class="brand-dot"></span>Lively Oak Dishes</div>
<p class="footer-about">Lorem ipsum dolor sit amet, consectetur adipiscing elit, sed do eiusmod tempor incididunt .</p>
<span class="social" style="left:121px"></span>
<span class="social" style="left:167px"></span>
<span class="social" style="left:218px"></span>

<span class="contact-icon" style="top:3188px">
  <svg width="20" height="20" viewBox="0 0 24 24"><path fill="#6dbd45" d="M6.6 10.8a15 15 0 0 0 6.6 6.6l2.2-2.2c.3-.3.7-.4 1-.2 1.1.4 2.3.6 3.6.6.6 0 1 .4 1 1V20c0 .6-.4 1-1 1A17 17 0 0 1 3 4c0-.6.4-1 1-1h3.5c.6 0 1 .4 1 1 0 1.3.2 2.5.6 3.6.1.3 0 .7-.2 1z"/></svg>
</span>
<span class="contact-text" style="top:3198px">0400 615 208</span>
<span class="contact-icon" style="top:3264px">
  <svg width="18" height="14" viewBox="0 0 18 14"><rect width="18" height="14" rx="1" fill="#6dbd45"/><path d="M1 1l8 6 8-6" stroke="#fff" stroke-width="1.5" fill="none"/></svg>
</span>
<span class="contact-text" style="top:3274px">hello@livelyoakdishes.com.au</span>
<span class="contact-icon" style="top:3336px">
  <svg width="22" height="22" viewBox="0 0 22 22" fill="none" stroke="#6dbd45" stroke-width="1.8"><circle cx="11" cy="11" r="9"/><path d="M11 5v6l4 2"/></svg>
</span>
<p class="contact-text" style="top:3344px;left:544px">Opening Hours<br><span style="margin-left:3px">Mon- Friday – 9 – 5 pm</span><br><span style="margin-left:3px">Sat – 8 am – 12 pm</span></p>

<span class="footer-link" style="top:3191px">Disclaimer</span>
<span class="footer-link" style="top:3234px">Terms &amp; Conditions</span>
<span class="footer-link" style="top:3277px">Privacy – Policy</span>
<span class="footer-mark">LOD</span>

<p class="copyright">© 2020 All Rights Reserved | Privacy Policy | Terms and Conditions</p>

</body>
</html>
```